Sell the dream! Property investment proposal document

We are looking for a proposal document which outlines our vision for property development. The purpose of the document is to raise investment from investors - sell the dream!
Brief summary:
Kestrel Dwellings Developments, is an emerging New Zealand property investment company with a focus on providing unique property investment opportunities.
Our expertise and capabilities in architectural modular homes provide us with a remarkable advantage in tackling the development of properties that are typically considered challenging, remote, or uniquely positioned.
Our specialization in this niche sector of property development not only sets us apart from competitors, but also paves the way for lucrative investment opportunities in the New Zealand property market.
Feel free to use any images from www.kestreldwellings.co.nz
Target Market(s)
investors for a unique property development opportunity
Industry/Entity Type
luxury property development in unique locations throughout New Zealand
Colors
Designer to choose only greyscale colors for use in the design.
Look and feel

```html
<!DOCTYPE html>
<html lang="en">
<head>
<meta charset="utf-8">
<title>Kestrel Dwellings – Investment Proposal Spreads</title>
<link href="https://fonts.googleapis.com/css2?family=Poppins:wght@300;400;600;700&family=Oswald:wght@600&display=swap" rel="stylesheet">
<style>
  :root{
    --page:#ffffff;
    --ink-warm:#2e2a27;
    --ink:#2b2b2b;
    --paper:#ffffff;
    --mute:#d9d9d9;
    --rule:#9a9a9a;
    --ghost:#f3f3f3;
  }
  *{box-sizing:border-box;margin:0;padding:0}
  html,body{width:891px;height:1200px;overflow:hidden;background:var(--page)}
  body{position:relative;font-family:'Poppins',sans-serif;color:var(--paper)}
  .spread{position:absolute;left:87px;width:718px;height:253px;overflow:hidden;background:var(--ink)}
  .spread--cover{top:130px;background:var(--paper)}
  .spread--intro{top:471px}
  .spread--value{top:813px}
  .abs{position:absolute}
  .photo{position:absolute}
  .rule-frame{position:absolute;border-color:var(--rule);border-style:solid;border-width:0}

  /* cover */
  .cover-back-top{left:0;top:0;width:359px;height:119px;background:var(--paper)}
  .cover-back-bottom{left:0;top:119px;width:359px;height:134px;background:var(--ink-warm)}
  .ghost-name{left:30px;top:-10px;font-weight:300;font-size:108px;color:var(--ghost);letter-spacing:-3px;line-height:1}
  .brand{font-family:'Poppins',sans-serif;font-weight:400;letter-spacing:-1.5px;line-height:1}
  .brand--back{left:118px;top:22px;font-size:32px;color:#2a2a2a}
  .brand--front{left:462px;top:22px;font-size:32px;color:var(--paper)}
  .contact{left:92px;width:176px;text-align:center;font-size:7.6px;line-height:10.7px;color:var(--paper);top:166px}
  .contact-icons{left:152px;top:151px;display:flex;gap:8px}
  .social{left:170px;top:199px;display:flex;gap:5px}
  .social span{width:7px;height:7px;border-radius:50%;background:var(--paper)}
  .web{font-size:8px;letter-spacing:2px;color:var(--paper);font-weight:300;white-space:nowrap}
  .web b{font-weight:600}
  .web--back{left:92px;width:176px;text-align:center;top:214px;font-size:7.8px;letter-spacing:1.6px}
  .web--front{left:459px;top:214px;font-size:7.8px;letter-spacing:1.6px}
  .cover-front-panel{left:449px;top:0;width:269px;height:253px;background:var(--ink-warm)}
  .headline{left:591px;top:90px;line-height:1}
  .headline .light{display:block;font-weight:300;font-size:17.5px;letter-spacing:.3px}
  .headline .condensed{display:block;font-family:'Oswald',sans-serif;font-weight:600;font-size:17.5px;margin-top:2px}
  .headline .heavy{display:block;font-weight:700;font-size:20px;margin-top:1px}
  .dash{left:592px;top:165px;width:10px;height:2px;background:var(--paper)}
  .lede{left:592px;top:174px;width:100px;font-size:4.2px;line-height:5.2px;color:var(--mute)}

  /* inner pages */
  .bar{position:absolute;width:2.5px;background:var(--paper)}
  .title{position:absolute;font-size:17px;line-height:1;font-weight:300;white-space:nowrap;letter-spacing:-.2px}
  .title b{font-weight:700}
  .copy{position:absolute;font-size:4.2px;line-height:5.1px;color:var(--mute)}
  .copy p+p{margin-top:4.6px}
  .footer{position:absolute;display:flex;align-items:center;gap:4px}
  .footer .web{font-size:6.2px;letter-spacing:1.4px}
  .footer .line{flex:1;height:.6px;background:var(--rule)}
  .folio{width:6px;height:8px;background:var(--paper);color:var(--ink);font-size:4px;font-weight:600;display:flex;align-items:center;justify-content:center}
</style>
</head>
<body>

<!-- Cover spread -->
<section class="spread spread--cover">
  <div class="abs cover-back-top"></div>
  <div class="abs ghost-name">Kestrel</div>
  <div class="abs cover-back-bottom"></div>
  <div class="abs brand brand--back">Kestrel</div>
  <div class="rule-frame" style="left:230px;top:59px;width:37px;height:22px;border-top-width:.6px;border-right-width:.6px"></div>
  <div class="rule-frame" style="left:92px;top:120px;width:58px;height:30px;border-left-width:.6px;border-bottom-width:.6px"></div>
  <div class="photo" role="img" aria-label="Aerial view of a long dark modular home on coastal farmland at dusk" style="left:99px;top:66px;width:161px;height:76px;border:1px solid #e8e3d8;background:linear-gradient(180deg,#b8ab92 0%,#8a7d5c 30%,#6d6234 60%,#4d4527 100%)"></div>
  <div class="abs contact-icons">
    <svg width="10" height="10" viewBox="0 0 10 10"><circle cx="5" cy="5" r="5" fill="#fff"/><path d="M3.3 2.6l1 .1.4 1.2-.6.5c.3.7.8 1.2 1.5 1.5l.5-.6 1.2.4.1 1c-2.4.3-4.4-1.7-4.1-4.1z" fill="#2e2a27"/></svg>
    <svg width="10" height="10" viewBox="0 0 10 10"><circle cx="5" cy="5" r="5" fill="#fff"/><rect x="2.7" y="3.3" width="4.6" height="3.4" fill="#2e2a27"/><path d="M2.8 3.4L5 5.2 7.2 3.4" stroke="#fff" stroke-width=".5" fill="none"/></svg>
    <svg width="10" height="10" viewBox="0 0 10 10"><circle cx="5" cy="5" r="5" fill="#fff"/><path d="M5 2.3a1.8 1.8 0 0 1 1.8 1.8C6.8 5.4 5 7.6 5 7.6S3.2 5.4 3.2 4.1A1.8 1.8 0 0 1 5 2.3z" fill="#2e2a27"/><circle cx="5" cy="4.1" r=".6" fill="#fff"/></svg>
  </div>
  <div class="abs contact">09 555 0142<br>sales@kestreldwellings.co.nz<br>Tarewa Valley, Auckland</div>
  <div class="abs social"><span></span><span></span></div>
  <div class="abs web web--back">www.<b>kestreldwellings</b>.co.nz</div>

  <div class="abs cover-front-panel"></div>
  <div class="rule-frame" style="left:349px;top:62px;width:100px;height:20px;border-top-width:.6px;border-left-width:.6px"></div>
  <div class="photo" role="img" aria-label="Dark timber-clad modular home above a concrete driveway with native garden" style="left:359px;top:72px;width:224px;height:131px;background:linear-gradient(180deg,#c9cdd0 0%,#8d9389 35%,#3c3d38 60%,#7c7f72 85%,#b3b2ab 100%)"></div>
  <div class="abs brand brand--front">Kestrel</div>
  <div class="rule-frame" style="left:577px;top:0;width:125px;height:80px;border-left-width:.6px;border-bottom-width:.6px"></div>
  <div class="photo" role="img" aria-label="Lounge chairs facing floor-to-ceiling windows over the sea" style="left:583px;top:0;width:135px;height:72px;background:linear-gradient(180deg,#a9c6dc 0%,#5f87a7 45%,#3a5d73 60%,#2f2b28 80%,#1e1c1b 100%)"></div>
  <div class="abs headline"><span class="light">MODULAR</span><span class="condensed">ARCHITECTURAL</span><span class="heavy">HOMES</span></div>
  <div class="abs dash"></div>
  <div class="abs lede">Kestrel Dwellings Developments, is an emerging New Zealand property investment company with a focus on providing unique property investment opportunities.</div>
  <div class="abs web web--front">www.<b>kestreldwellings</b>.co.nz</div>
</section>

<!-- Overview / origins spread -->
<section class="spread spread--intro">
  <div class="bar" style="left:26px;top:0;height:40px"></div>
  <h2 class="title" style="left:37px;top:25px">BUSINESS <b>OVERVIEW</b></h2>
  <div class="rule-frame" style="left:106px;top:51px;width:125px;height:147px;border-top-width:.6px;border-right-width:.6px"></div>
  <div class="photo" role="img" aria-label="Open living room with glass walls framing green hills and a harbour" style="left:0;top:60px;width:224px;height:131px;background:linear-gradient(180deg,#c4d3dc 0%,#9fb2bd 30%,#6c7f5a 50%,#8ea15c 70%,#8a6a4e 88%,#4a3a2d 100%)"></div>
  <div class="copy" style="left:237px;top:66px;width:98px">
    <p>Our expertise and capabilities in architectural modular homes provide us with a remarkable advantage in tackling the development of properties that are typically considered challenging, remote, or uniquely positioned.</p>
    <p>As a company, with 48 employees boasting a wealth of experience in handling complex architectural projects, making us well -equipped to navigate the intricacies and demands of such ventures.</p>
    <p>This advantage allows us to not only execute projects efficiently but also to deliver exceptional results within condensed time frames.</p>
    <p>By capitalizing on our ability to develop difficult, remote, or one-of-a-kind properties swiftly and effectively, Kestrel Dwellings Developments offers investors a rare chance to engage in projects that promise exceptional profitability in the New Zealand property market.</p>
  </div>
  <div class="copy" style="left:25px;top:205px;width:305px">Our specialization in this niche sector of property development not only sets us apart from competitors, but also paves the way for lucrative investment opportunities in the New Zealand property market.</div>
  <div class="footer" style="left:25px;top:223px;width:311px"><span class="web">www.<b>kestreldwellings</b>.co.nz</span><span class="line"></span><span class="folio">1</span></div>

  <div class="bar" style="left:385px;top:0;height:52px"></div>
  <h2 class="title" style="left:397px;top:19px;line-height:17px">BUSINESS<br><b>ORIGINS</b></h2>
  <div class="copy" style="left:384px;top:66px;width:138px">
    <p>Kestrel Dwellings Developments was established with the goal of transforming the property investment market in New Zealand by introducing an innovative approach that centers on architectural modular designs and streamlined project timelines.</p>
    <p>Driven by our enthusiasm for architecture and real estate, we have expanded our successful business model to not only offer financial opportunities for investors but also to expand on our passion for high-end architectural design.</p>
    <p>With a wealth of experience accumulated over the past six years in the construction and the property market, we are pivoting to focus solely on our property development initiatives, presenting completed Kestrel projects to the market, in exclusive locations.</p>
    <p>These projects will boast high-quality standards, meticulous attention to detail and landscaping, and creative design elements.</p>
    <p>By introducing completed Kestrel properties into the market, we aim to reach a wider audience, catering to individuals who prefer ready-to-occupy homes, over engaging in the design and construction process. This approach also simplifies the financing process for prospective buyers, as established properties are often preferred by financial lenders.</p>
  </div>
  <div class="photo" role="img" aria-label="Interior with glass corner walls opening onto misty mountain slopes, armchair and hide rug" style="left:543px;top:0;width:175px;height:253px;background:linear-gradient(160deg,#3a3633 0%,#8c8a82 25%,#a39a86 45%,#6b6258 65%,#2e2c2a 85%,#5a5652 100%)"></div>
  <div class="footer" style="left:384px;top:224px;width:159px"><span class="web">www.<b>kestreldwellings</b>.co.nz</span><span class="line"></span></div>
  <div class="abs folio" style="left:688px;top:225px">2</div>
</section>

<!-- Advantage / financial spread -->
<section class="spread spread--value">
  <div class="rule-frame" style="left:131px;top:13px;width:125px;height:18px;border-top-width:.6px;border-right-width:.6px"></div>
  <div class="rule-frame" style="left:105px;top:105px;width:95px;height:35px;border-left-width:.6px;border-bottom-width:.6px"></div>
  <div class="photo" role="img" aria-label="Glass pavilion home on a headland at sunset" style="left:25px;top:31px;width:87px;height:94px;background:linear-gradient(180deg,#b7c2cc 0%,#d6c3a3 35%,#8b8a86 60%,#4d4a46 80%,#7a7268 100%)"></div>
  <div class="photo" role="img" aria-label="Cantilevered dark modular home above a grassy slope with rocks" style="left:112px;top:22px;width:138px;height:112px;background:linear-gradient(180deg,#f3f4f5 0%,#e4e7e9 25%,#3b3b3b 42%,#55604a 60%,#7f9a4d 80%,#93ad55 100%)"></div>
  <div class="photo" role="img" aria-label="Low black home with a covered terrace among tall grasses" style="left:250px;top:31px;width:83px;height:94px;background:linear-gradient(180deg,#eceeef 0%,#dfe2e3 40%,#3a3a38 58%,#5f5b45 78%,#8d7f52 100%)"></div>
  <h2 class="title" style="left:25px;top:150px;font-size:17.5px">COMPETITIVE <b>ADVANTAGE</b></h2>
  <div class="copy" style="left:25px;top:175px;width:310px">
    <p>Our competitive advantage lies in the uniqueness of our property investment opportunities. Unlike traditional real estate companies, we focus on offering properties that are not only profitable but also aesthetically pleasing and unique. By catering to the tastes of architecture lovers, we set ourselves apart from the competition and attract a niche market of customers who appreciate the artistry and design of our projects.</p>
    <p>Additionally, the streamlined and condensed timelines facilitated by our modular approach provide quicker returns on investment.</p>
  </div>
  <div class="footer" style="left:25px;top:223px;width:311px"><span class="web">www.<b>kestreldwellings</b>.co.nz</span><span class="line"></span><span class="folio">3</span></div>

  <div class="rule-frame" style="left:595px;top:48px;width:107px;height:80px;border-right-width:.6px;border-bottom-width:.6px;border-bottom-color:var(--rule)"></div>
  <div class="photo" role="img" aria-label="Minimal lounge with cream sofas and a low table facing a wide sea view" style="left:383px;top:0;width:308px;height:120px;background:linear-gradient(180deg,#8d8a87 0%,#c9c6c4 25%,#b3b0ae 45%,#a89c90 60%,#6e655d 80%,#4a4541 100%)"></div>
  <h2 class="title" style="left:383px;top:131px">FINANCIAL <b>SUMMARY</b></h2>
  <div class="copy" style="left:384px;top:155px;width:312px">
    <p>In terms of financial projections, with each development, we anticipate a profit of 10%-20% which will be project dependent.</p>
    <p>This growth is fueled by the increasing demand for unique property investments in New Zealand and our ability to deliver high-quality services to the market in a condensed time frame, with heavily controlled costs.</p>
    <p>With a solid business model and a dedicated team, we are confident in our ability to achieve success and establish Kestrel Dwellings Investments as a trusted name in the industry.</p>
    <p>New Zealand's property market has been experiencing steady growth over the years, making it an attractive destination for property investors. With its beautiful landscapes and strong economy, New Zealand offers a diverse range of investment opportunities for both local and international investors. The demand for quality properties in prime locations continues to rise, creating a favorable environment for property investment companies like ours that can lean on our modular benefits of being able to reach unique and remote locations.</p>
  </div>
  <div class="footer" style="left:384px;top:225px;width:312px"><span class="web">www.<b>kestreldwellings</b>.co.nz</span><span class="line"></span><span class="folio">4</span></div>
</section>

</body>
</html>
```